Candle Rental Business seeks new website design

We need a new website design for a Candle hire business. The business rents out pillar candles for events such as weddings and corporate events. Our main target market is weddings. The business name is Hire a Lantern. The business name does not have a logo design.

We would like a website that is light in colours and creates a warm atmosphere. The design needs to be elegant and upmarket. There are different size candles that we hire out, ranging from 10cm diameter to 20cm diameter, flat, tall etc. All our candles are white in colour. Its just the size that differs.

We would also like to include a section for hiring out decor such as glassvases, candlebras, overlays and chairs sachets, chair covers. However, this is not the businesses main focus but an additional offering to customers.

Target Market(s)

Wedding venues and brides. Corporate events. School dances.

Industry/Entity Type

Hospitality

Logo Text

Hire a Lantern

Number of Pages Required

1 page

Font styles to use
Sans Serif
Script

Requirements
Must have
• Pictures of pillar candles. Plain white candles. The website must centre around candles.
Nice to have
• Different examples of candle centrepieces
Should not have
• Pictures must not be of brides. Pictures of surrounding is perferable.

```html
<!DOCTYPE html>
<html lang="en">
<head>
<meta charset="utf-8">
<title>Hire a Lantern</title>
<link rel="stylesheet" href="https://fonts.googleapis.com/css2?family=Lato:wght@300;400;700;900&display=swap">
<style>
:root{
  --orange:#f07c0f;
  --amber:#f9b115;
  --ink:#222;
  --text:#555;
  --muted:#777;
  --light:#eeeeee;
  --dark:#2d2d2d;
  --white:#fff;
  --line:#cfcfcf;
}
*{box-sizing:border-box;margin:0;padding:0}
html,body{width:1200px;height:2727px;overflow:hidden}
body{position:relative;font-family:"Lato",sans-serif;color:var(--text);background:var(--white)}
.abs{position:absolute}
a{color:inherit;text-decoration:none}

/* header */
.site-header{left:0;top:0;width:1200px;height:86px;background:var(--white)}
.brand{left:80px;top:18px;display:flex;align-items:center;gap:12px}
.brand-mark{width:26px;height:26px;background:var(--orange);border-radius:50%}
.brand-name{font-size:36px;font-weight:400;color:var(--ink);letter-spacing:.3px}
.account{top:10px;right:46px;display:flex;gap:36px;font-size:13px;color:var(--muted)}
.account span{display:flex;align-items:center;gap:7px}
.main-nav{top:50px;left:680px;display:flex;font-size:15px;color:var(--ink)}
.main-nav a{padding:4px 7px;margin-right:26px}
.main-nav a.active{color:var(--orange);border:1.5px solid var(--orange)}
.main-nav a:last-child{margin-right:0}

/* hero */
.hero{left:0;top:86px;width:1200px;height:534px;
  background:radial-gradient(ellipse at 30% 40%,#8a6040 0%,#4a2e1c 45%,#1e120a 100%)}
.hero-title{left:0;top:370px;width:1200px;text-align:center;color:var(--white);font-size:40px;font-weight:900}
.hero-sub{left:0;top:438px;width:1200px;text-align:center;color:var(--white);font-size:30px;font-weight:400}
.btn{display:inline-flex;align-items:center;justify-content:center;color:var(--white);font-size:15px}
.btn-amber{background:var(--amber)}
.btn-orange{background:var(--orange)}
.hero-btn{left:522px;top:505px;width:156px;height:44px;font-size:19px}

/* section headings */
.section-title{left:0;width:1200px;text-align:center;font-size:41px;font-weight:400;color:var(--ink)}

/* about */
.about-copy{left:84px;top:730px;width:1032px;text-align:center;font-size:14px;line-height:26px;color:var(--text)}
.about-btn{left:542px;top:827px;width:116px;height:39px;font-size:15px}

/* products */
.products{left:0;top:915px;width:1200px;height:630px;
  background:linear-gradient(180deg,#5a4638 0%,#7b6556 50%,#4c3b30 100%)}
.products .section-title{color:var(--white);top:50px}
.product-card{top:136px;width:338px;height:451px;background:var(--white);padding:9px}
.product-photo{width:320px;height:205px}
.product-name{margin:16px 0 0 1px;font-size:21px;font-weight:700;color:var(--orange)}
.product-text{margin-top:8px;font-size:13px;line-height:26px;color:var(--text);width:288px}
.product-actions{position:absolute;left:11px;top:383px;display:flex;gap:11px}
.product-actions .btn{width:116px;height:40px}

/* how it works */
.step{width:150px;height:150px;border-radius:50%;display:flex;align-items:center;justify-content:center}
.step-label{width:220px;text-align:center;font-size:22px;line-height:29px;color:var(--muted)}

/* decor */
.decor-band{left:0;top:2002px;width:1200px;height:676px;background:var(--light)}
.decor-tile{top:2154px;width:255px;height:188px;display:flex;align-items:center;justify-content:center}
.decor-tile::after{content:"";position:absolute;inset:8px;border:1.5px solid rgba(255,255,255,.75)}
.decor-name{position:relative;z-index:1;color:var(--white);font-size:22px;font-weight:700;text-align:center;line-height:30px}

/* footer */
.footer-rule{left:58px;top:2396px;width:1084px;height:1px;background:var(--line)}
.footer-head{top:2423px;font-size:15px;font-weight:400;color:var(--ink)}
.quick-links{left:80px;top:2462px;list-style:none;font-size:12.5px;color:var(--text)}
.quick-links li{margin-bottom:16px;display:flex;align-items:center;gap:12px}
.quick-links li::before{content:"";width:5px;height:5px;border:1px solid var(--muted);border-radius:50%}
.contact-row{left:304px;display:flex;align-items:flex-start;gap:13px;font-size:13px;line-height:19px;color:var(--text)}
.field{left:651px;width:238px;border:1.5px solid #999;background:var(--white);font-size:12px;color:var(--muted);padding:6px 9px}
.submit{left:651px;top:2622px;width:238px;height:30px;font-size:15px}
.social{left:1002px;display:flex;align-items:center;gap:14px;font-size:12.5px}
.social i{width:32px;height:32px;border-radius:50%;display:block}
.bottom-bar{left:0;top:2678px;width:1200px;height:49px;background:var(--dark);color:#ddd;font-size:14px}
.copyright{left:80px;top:15px}
.payments{right:80px;top:12px;display:flex;align-items:center;gap:5px}
.payments span{margin-right:14px}
.card-chip{width:30px;height:20px;background:#f4f4f4;border-radius:2px}
</style>
</head>
<body>

<header class="site-header abs">
  <div class="brand abs"><span class="brand-mark"></span><span class="brand-name">Hire a Lantern</span></div>
  <div class="account abs">
    <span><svg width="14" height="14" viewBox="0 0 14 14" fill="none" stroke="#777" stroke-width="1.3"><path d="M8 1h5v12H8"/><path d="M1 7h8M6 4l3 3-3 3"/></svg>Log In</span>
    <span><svg width="14" height="14" viewBox="0 0 14 14" fill="none" stroke="#777" stroke-width="1.3"><rect x="1.5" y="1.5" width="11" height="11"/><path d="M4 5h6M4 8h6M4 11h3"/></svg>Register</span>
  </div>
  <nav class="main-nav abs">
    <a class="active" href="#">Home</a>
    <a href="#">About Us</a>
    <a href="#">Our Products</a>
    <a href="#">Contact Us</a>
  </nav>
</header>

<section class="hero abs" role="img" aria-label="Candlelit reception table with glass lanterns, roses and white pillar candles"></section>
<h1 class="hero-title abs">There Are Two Ways of Spreading Light:</h1>
<p class="hero-sub abs">To Be The Candle Or The Mirror That Reflects It</p>
<a class="btn btn-amber hero-btn abs" href="#">Buy Online</a>

<h2 class="section-title abs" style="top:666px">About Us</h2>
<p class="about-copy abs">We are a family owned and operated company and began making decorative candles for all occasions.&nbsp;&nbsp; All of our candles are individually hand made in our candle studio, situated in Brookhaven, outside Larchmont.&nbsp; Our wax is local and of a very high quality, and dripless! Our wax is also made with a high melting point, which means it will not melt or bend in hot temperatures.</p>
<a class="btn btn-orange about-btn abs" href="#">Read More</a>

<section class="products abs" role="img" aria-label="Dim banquet table with glassware and candles in warm brown tones">
  <h2 class="section-title abs">Our Products</h2>
  <article class="product-card abs" style="left:80px">
    <div class="product-photo" role="img" aria-label="Large white pillar candle among cream roses on a garden table" style="background:linear-gradient(180deg,#c9d3a6,#e9e3cc 55%,#9fae6a)"></div>
    <h3 class="product-name">Hire Candles</h3>
    <p class="product-text">Do you love using candles for your events but tired of sorting old used candles or buying expensive candles. Believe it or not you can now rent candles.</p>
    <div class="product-actions"><a class="btn btn-orange" href="#">Buy Now</a><a class="btn btn-amber" href="#">More Info</a></div>
  </article>
  <article class="product-card abs" style="left:431px">
    <div class="product-photo" role="img" aria-label="White ball candles resting in two round glass holders" style="background:linear-gradient(180deg,#5c4a40,#8a7264 60%,#b79f90)"></div>
    <h3 class="product-name">Personalised Candles</h3>
    <p class="product-text">Do you love using candles for your events but tired of sorting old used candles or buying expensive candles. Believe it or not you can now rent candles.</p>
    <div class="product-actions"><a class="btn btn-orange" href="#">Buy Now</a><a class="btn btn-amber" href="#">More Info</a></div>
  </article>
  <article class="product-card abs" style="left:780px">
    <div class="product-photo" role="img" aria-label="Green and black pillar candles on a silver stand" style="background:linear-gradient(180deg,#e8e8e6,#d4d5cf 55%,#8d9a56)"></div>
    <h3 class="product-name">Décor Hire</h3>
    <p class="product-text">Do you love using candles for your events but tired of sorting old used candles or buying expensive candles. Believe it or not you can now rent candles.</p>
    <div class="product-actions"><a class="btn btn-orange" href="#">Buy Now</a><a class="btn btn-amber" href="#">More Info</a></div>
  </article>
</section>

<h2 class="section-title abs" style="top:1592px">How It Works</h2>
<svg class="abs" style="left:0;top:1680px" width="1200" height="240" viewBox="0 0 1200 240" fill="none" stroke="#d6d6d6" stroke-width="3">
  <path d="M250 32 Q300 14 352 24"/><path d="M337 14 L352 24 L338 36"/>
  <path d="M550 216 Q600 200 650 206"/><path d="M636 196 L650 206 L637 218"/>
  <path d="M848 32 Q900 14 950 24"/><path d="M935 14 L950 24 L936 36"/>
</svg>

<div class="step abs" style="left:80px;top:1721px;background:var(--orange)">
  <svg width="60" height="80" viewBox="0 0 60 80" fill="#fff"><path d="M30 4c7 9 7 15 0 19-7-4-7-10 0-19z"/><rect x="14" y="30" width="32" height="46" rx="3"/><path d="M14 42h32M14 56h32" stroke="#f07c0f" stroke-width="3"/></svg>
</div>
<div class="step abs" style="left:376px;top:1721px;background:var(--amber)">
  <svg width="66" height="80" viewBox="0 0 66 80" fill="#fff"><path d="M22 10a6 6 0 0 1 12 0v26h2V30a6 6 0 0 1 11 0v8a6 6 0 0 1 11 2v20c0 10-7 18-18 18H32c-8 0-12-4-16-10L6 52a6 6 0 0 1 9-7l7 7z"/></svg>
</div>
<div class="step abs" style="left:676px;top:1721px;background:var(--orange)">
  <svg width="84" height="60" viewBox="0 0 84 60" fill="none" stroke="#fff" stroke-width="4"><rect x="8" y="14" width="68" height="38" rx="3" transform="rotate(-10 42 33)"/><circle cx="42" cy="33" r="9"/><path d="M18 27v12M66 27v12"/></svg>
</div>
<div class="step abs" style="left:970px;top:1721px;background:var(--amber)">
  <svg width="70" height="80" viewBox="0 0 70 80" fill="#fff"><path d="M35 4c6 8 6 13 0 17-6-4-6-9 0-17z"/><rect x="24" y="26" width="22" height="34" rx="2"/><path d="M8 62h54l-6 8H14z"/><rect x="30" y="70" width="10" height="6"/></svg>
</div>

<p class="step-label abs" style="left:45px;top:1895px">Choose your<br>Candle</p>
<p class="step-label abs" style="left:341px;top:1895px">Book your<br>Candle</p>
<p class="step-label abs" style="left:641px;top:1895px">Make<br>payment</p>
<p class="step-label abs" style="left:935px;top:1880px">Light Up<br>Your Event</p>

<div class="decor-band abs"></div>
<h2 class="section-title abs" style="top:2050px">Our Hiring Out Decor</h2>
<div class="decor-tile abs" style="left:80px" role="img" aria-label="Tall glass vases holding lit candles"><div style="position:absolute;inset:0;background:linear-gradient(135deg,#2b2f3a,#6e7480 55%,#2a2a30)"></div><span class="decor-name">Glass Vases</span></div>
<div class="decor-tile abs" style="left:342px" role="img" aria-label="Glass candelabras on a table"><div style="position:absolute;inset:0;background:linear-gradient(135deg,#6b5b3a,#a08d66 55%,#5c4e33)"></div><span class="decor-name">Candle Bras</span></div>
<div class="decor-tile abs" style="left:604px" role="img" aria-label="Lace overlay tied around a chair"><div style="position:absolute;inset:0;background:linear-gradient(135deg,#3a3a3a,#8c8c8c 50%,#2e2e2e)"></div><span class="decor-name">Overlays &amp;<br>Chairs Sachets</span></div>
<div class="decor-tile abs" style="left:865px" role="img" aria-label="Rows of chairs with pink chair covers"><div style="position:absolute;inset:0;background:linear-gradient(135deg,#4a3a40,#b58a95 55%,#3d3035)"></div><span class="decor-name">Chair Covers</span></div>

<div class="footer-rule abs"></div>
<h4 class="footer-head abs" style="left:80px">Quick Links</h4>
<ul class="quick-links abs"><li>Home</li><li>About Us</li><li>Our Products</li><li>Contact Us</li></ul>

<h4 class="footer-head abs" style="left:304px">Contact Details</h4>
<div class="contact-row abs" style="top:2460px">
  <svg width="18" height="22" viewBox="0 0 18 22" fill="none" stroke="#888" stroke-width="1.6"><path d="M9 21s7-7 7-12A7 7 0 0 0 2 9c0 5 7 12 7 12z"/><circle cx="9" cy="9" r="2.5"/></svg>
  <span>1/23 Lorem Ips Dolo, Consecer<br>wererr Nonuy - 12345</span>
</div>
<div class="contact-row abs" style="top:2511px">
  <svg width="18" height="20" viewBox="0 0 18 20" fill="none" stroke="#888" stroke-width="1.6"><path d="M5 2l3 4-2 2c1 3 3 5 6 6l2-2 3 3-2 3C8 18 1 10 2 4z"/></svg>
  <span>123-456-7890</span>
</div>
<div class="contact-row abs" style="top:2554px">
  <svg width="18" height="14" viewBox="0 0 18 14" fill="none" stroke="#888" stroke-width="1.6"><rect x="1" y="1" width="16" height="12"/><path d="M1 1l8 7 8-7"/></svg>
  <span>info@companyname.com</span>
</div>

<h4 class="footer-head abs" style="left:652px">Quick Inquiry</h4>
<div class="field abs" style="top:2463px;height:31px">Name</div>
<div class="field abs" style="top:2502px;height:31px">Phone</div>
<div class="field abs" style="top:2540px;height:73px">Message</div>
<a class="btn btn-orange submit abs" href="#">Submit</a>

<h4 class="footer-head abs" style="left:1002px">Follow Us</h4>
<div class="social abs" style="top:2464px;color:#3b5998"><i style="background:#3b5998"></i>Fanpage</div>
<div class="social abs" style="top:2503px;color:#3fb6e8"><i style="background:#3fb6e8"></i>Chirper</div>
<div class="social abs" style="top:2542px;color:#1c87bd"><i style="background:#1c87bd"></i>Linkwork</div>
<div class="social abs" style="top:2581px;color:#d34836"><i style="background:#d34836"></i>Circles Plus</div>

<footer class="bottom-bar abs">
  <p class="copyright abs">Copyright © 2016 Hire a Lantern. All Rights Reserved.</p>
  <div class="payments abs"><span>We Accept:</span><i class="card-chip"></i><i class="card-chip"></i><i class="card-chip"></i><i class="card-chip"></i></div>
</footer>

</body>
</html>
```